Trifold Brochure for orthodontic practice

We need a new brochure for an orthodontic office in Avon, CT USA. The target of this brochure is for children, adolescents, and their family seeking orthodontic care. There flyer will be distributed to new patients and in local dental and pediatric dental offices. Emphasize individualized patient care; warm friendly environment; board certified orthodontist, a specialty practice, all digital diagnostic records included dental model (Vexal scanner) and digital radiography. The content from the old flyer can be used for a reference and resource for the write up, although we are looking for briefer wording in the new flyer. Some stock photos are included, I have accounts with Quillo, pixmera, and snapvaultpics so other images can be licensed and included. The goal is an eye-catching, informative brochure that will attract new patients. More information about our practice can be found at dransfeldorthodontics-example.com. Information from the website can be included

Target Market(s)

Parents of children and adolescents that are seeking orthodontic care; referring dentists

Font styles to use
Serif
Sans Serif

Requirements
Must have
• Our logo CMYK codes are: Purple C:99, M:90, Y:11, K:04, Green: C:35, M:0, Y:100, K:22, Blue: C:64, M:46, Y:0, K:0. These colors are consistent with our business card. But colorful and bright is welcome and encouraged especially when color scheme is complementary to logo colors
• Easy to read
Nice to have
• Diverse photos of smiling children, attractive photos of children with braces
• Inspire reader to call for an appointment!
Should not have
• Dorky dental photos

```html
<!DOCTYPE html>
<html lang="en">
<head>
<meta charset="utf-8">
<title>Dransfeld Orthodontics – Trifold Brochure</title>
<link rel="stylesheet" href="https://fonts.googleapis.com/css2?family=Lora:ital,wght@0,600;0,700;1,500;1,600&family=Source+Sans+3:wght@400;600&display=swap">
<style>
  :root{
    --stage:#e4e4e4;
    --navy:#1f3572;
    --blue:#2a5aa8;
    --green:#3f9b3a;
    --lime:#d6f64a;
    --paper:#f7f8fa;
    --ink:#1b2450;
    --white:#ffffff;
    --serif:'Lora', Georgia, serif;
    --sans:'Source Sans 3', Arial, sans-serif;
  }
  *{box-sizing:border-box;margin:0;padding:0}
  html,body{width:1200px;height:800px;overflow:hidden;background:var(--stage)}
  .brochure{position:absolute;left:100px;top:40px;width:1000px;height:720px;overflow:hidden;box-shadow:0 6px 20px rgba(0,0,0,.18)}
  .brochure-art{position:absolute;inset:0}
  .headline{position:absolute;left:24px;top:26px;font-family:var(--serif);font-weight:700;font-size:33px;color:var(--white);letter-spacing:.2px}
  .intro{position:absolute;left:24px;top:80px;width:300px;font-family:var(--sans);font-size:11px;line-height:1.35;color:var(--white)}
  .bio{position:absolute;left:22px;top:238px;width:296px;font-family:var(--sans);font-size:8.2px;line-height:1.28;color:var(--ink);text-align:justify}
  .bio p{margin-bottom:4px}
  .portrait{float:left;width:138px;height:150px;margin:2px 9px 4px 0;background:#8fa9c4}
  .logo{position:absolute;left:432px;top:238px;display:flex;align-items:center;gap:7px}
  .logo-dot{width:12px;height:12px;border-radius:50%;background:var(--green)}
  .logo-name{font-family:var(--sans);font-weight:600;font-size:12px;letter-spacing:1px;color:var(--navy);font-variant:small-caps}
  .section-title{font-family:var(--serif);font-style:italic;font-weight:600;color:var(--navy)}
  .treatment-title{position:absolute;left:354px;top:264px;font-size:20px}
  .treatment-title span{font-style:normal;text-transform:uppercase;font-size:17px}
  .treatment-text{position:absolute;left:354px;top:294px;width:290px;font-family:var(--sans);font-size:9px;line-height:1.3;color:var(--ink)}
  .services-title{position:absolute;left:354px;top:376px;font-size:19px}
  .services-list{position:absolute;left:362px;top:404px;list-style:none;font-family:var(--serif);font-style:italic;font-weight:500;font-size:12px;line-height:1.2;color:var(--navy)}
  .circle-label{position:absolute;font-family:var(--serif);font-size:8px;letter-spacing:.6px;color:var(--ink);text-transform:uppercase}
</style>
</head>
<body>
<main class="brochure">
  <svg class="brochure-art" viewBox="0 0 1000 720" width="1000" height="720">
    <defs>
      <linearGradient id="photoTone" x1="0" y1="0" x2="1" y2="1">
        <stop offset="0" stop-color="#f4eee6"/>
        <stop offset=".5" stop-color="#e9c9ae"/>
        <stop offset="1" stop-color="#dfe6ee"/>
      </linearGradient>
      <linearGradient id="limeBand" x1="0" y1="0" x2="0" y2="1">
        <stop offset="0" stop-color="#8ccf2e"/>
        <stop offset="1" stop-color="#d6f64a"/>
      </linearGradient>
      <linearGradient id="blueSweep" x1="0" y1="0" x2="1" y2="1">
        <stop offset="0" stop-color="#2f64b4"/>
        <stop offset="1" stop-color="#1f3572"/>
      </linearGradient>
    </defs>

    <rect class="panel-photo" x="666" y="0" width="334" height="720" fill="url(#photoTone)" role="img" aria-label="Photo of three smiling teenagers leaning in together, seen from below"/>
    <rect class="panel-inside" x="333" y="0" width="333" height="720" fill="var(--paper)"/>
    <rect class="panel-about" x="0" y="0" width="333" height="720" fill="var(--lime)"/>
    <path class="lime-band" d="M0 200 C180 190 300 235 420 250 L420 300 C300 285 180 235 0 250 Z" fill="url(#limeBand)"/>
    <rect class="panel-about-fill" x="0" y="250" width="333" height="470" fill="var(--lime)"/>

    <path class="wave-green" d="M0 0 H1000 V76 C880 56 760 76 660 136 C560 196 500 276 420 266 C300 251 180 206 0 216 Z" fill="var(--green)"/>
    <path class="wave-navy" d="M0 0 H1000 V60 C880 40 760 60 660 120 C560 180 500 260 420 250 C300 235 180 190 0 200 Z" fill="url(#blueSweep)"/>

    <path class="wave-bottom" d="M430 720 C500 690 560 640 620 600 C720 540 850 515 1000 535 V720 Z" fill="url(#blueSweep)"/>

    <g class="service-circles">
      <circle cx="400" cy="664" r="46" fill="var(--white)"/>
      <circle cx="400" cy="664" r="40" fill="#e8c8ae" role="img" aria-label="Photo of a smiling young girl"/>
      <circle cx="515" cy="606" r="42" fill="var(--white)"/>
      <circle cx="515" cy="606" r="36" fill="#d98c8c" role="img" aria-label="Close-up photo of a smile with metal braces"/>
      <circle cx="615" cy="544" r="44" fill="var(--white)"/>
      <circle cx="615" cy="544" r="38" fill="#d97f7f" role="img" aria-label="Close-up photo of a smile with clear aligners"/>
    </g>
  </svg>

  <h1 class="headline">Your smile is our top priority!</h1>
  <p class="intro">Our dental practice is committed to providing exceptional orthodontic treatment in a warm, friendly and supportive environment. Whether you are an adult, adolescent or child, we recognize that every patient is unique and has specific concerns. Our entire team is dedicated to helping each patient address those needs and obtain the beautiful, healthy smile they have always wanted!</p>

  <div class="bio">
    <div class="portrait" role="img" aria-label="Portrait photo of Dr. Dransfeld"></div>
    <p>Dr. Dransfeld started his orthodontic career as a full-time professor at the Eastfield State University in 1992. At ESU, his interests in the biomechanics of orthodontic treatment developed. As an active scientific investigator of the role of biomechanics in orthodontic therapy, Dr. Dransfeld has contributed many scientific articles and chapters in orthodontic textbooks, and has given numerous regional, national, and international presentations. Dr. Dransfeld continues to collaborate in research, developing new scientific innovations aimed at increasing the efficiency and effectiveness of orthodontic care.</p>
    <p>Dr. Dransfeld graduated cum laude with a B.A. in Biology and Psychology from Marlow College in 1984 and earned his D.M.D. from the Eastfield State University in 1989. He continued his specialty training in orthodontics at the Eastfield State University where he completed his Master's of Dental Science degree in 1992.</p>
    <p>Dr. Dransfeld is a Diplomate of the National Board of Orthodontic Specialists. He is also on the editorial review board for the Journal of Facial Orthodontic Care and the Occlusion Review. We are also excited to share that Dr. Dransfeld was once again selected for Valley Living Magazine's Top Dentists!</p>
    <p>Dr. Dransfeld is a life-long resident of the valley. He was raised in Millbrook and is a graduate from Ridgeline Regional High School. There are few places he'd rather be than on a whitewater river. He has spent most of his life in or on water, a competitive swimmer through college and now an avid whitewater kayaker. Anytime he can, he gets outside, no matter the weather.</p>
    <p>Dr. Dransfeld lives in Elmford with his wife, Clara and daughters, Nora and Maisie.</p>
  </div>

  <div class="logo"><span class="logo-dot"></span><span class="logo-name">Dransfeld Orthodontics</span></div>

  <h2 class="section-title treatment-title">Personalized <span>Treatment</span></h2>
  <p class="treatment-text">We understand that each individual has specific concerns, issues, and goals when it comes to achieving a brilliant, attractive smile. Dr. Dransfeld will take all the necessary time to speak with each patient, learn more about their desired goals, and put together a comprehensive plan to help them achieve a smile that is both healthy and beautiful. He may recommend a single treatment, or may combine various techniques, depending on the individual needs of the patient.</p>

  <h2 class="section-title services-title">Our Scope of Services</h2>
  <ul class="services-list">
    <li>Various Types of Orthodontics</li>
    <li>Emergency Care ClearFit®</li>
    <li>Clear Aligners</li>
    <li>Metal Braces</li>
    <li>Tips on Caring for Braces</li>
    <li>Orthognathic Surgery</li>
    <li>Palatal Expander</li>
    <li>Lumina™ ADVANCED</li>
    <li>Ceramic Braces</li>
  </ul>

  <span class="circle-label" style="left:362px;top:606px">Orthodontics</span>
  <span class="circle-label" style="left:484px;top:552px">Metal Braces</span>
  <span class="circle-label" style="left:592px;top:486px">ClearFit®</span>
</main>
</body>
</html>
```